THE PAPER HERONS - creative phenoms who raise design to high art form.

Coffee-table book format.Will feature 20 'design' companies, one from each of 20 categories:3D Design . Branding Design . Broadcast Design . Communication . Digital Design Fashion . Exhibition Design . Furniture Design . Graphic Design . Industrial Design Interior Design . Jewelry . Lighting Design . Package Design . Retail Design . Sustainable Design . Urban Design . Web Design . Yacht DesignWant an eye-catching photo(s), design, etc. This will involve some creative effort.
Updates

After some thought, decided something that is a common thread through all design industries. A nice desk, upon which is a blank sketch pad, a pencil, and beside them a computer. A designer has a new idea, uses the sketch pad, then moves on to the computer to develop his/her idea. Cheers, Gordon

Target Market(s)

US professionals who own companies involved in the world of design.

Requirements
Must have
• Format is 11 in wide and 10 inches high cover.
• Photograph(s) or artwork that will catch the eye of the
• readers browsing the book sections.

```html
<!DOCTYPE html>
<html lang="en">
<head>
<meta charset="utf-8">
<title>The Paper Herons — Book Cover</title>
<link rel="stylesheet" href="https://fonts.googleapis.com/css2?family=Jost:wght@200;300;400;600&display=swap">
<style>
  :root {
    --spine-green: #7ab55c;
    --author-green: #7ab55c;
    --title-grey: #8e8e8e;
    --subtitle-ink: #1e1e1e;
    --paper: #ffffff;
    --spine-text: #ffffff;
  }
  * { margin: 0; padding: 0; box-sizing: border-box; }
  html, body {
    width: 1200px; height: 1015px; overflow: hidden; background: var(--paper);
  }
  .book-cover {
    position: relative; width: 1200px; height: 1015px; background: var(--paper);
    font-family: "Jost", sans-serif;
  }
  .spine {
    position: absolute; left: 0; top: 0; width: 68px; height: 1015px;
    background: var(--spine-green);
  }
  .spine-title, .spine-author {
    position: absolute; left: 34px; color: var(--spine-text);
    white-space: nowrap; transform-origin: 0 0;
    transform: rotate(90deg) translateY(-50%);
  }
  .spine-title {
    top: 90px; font-size: 27px; font-weight: 300; letter-spacing: 0.04em;
  }
  .spine-author {
    top: 726px; font-size: 16px; font-weight: 600; letter-spacing: 0.06em;
  }
  .front {
    position: absolute; left: 68px; top: 0; width: 1132px; height: 1015px;
    text-align: center;
  }
  .author {
    position: absolute; top: 48px; left: 0; width: 100%;
    font-size: 44px; font-weight: 300; letter-spacing: 0.42em;
    color: var(--author-green); line-height: 1; padding-left: 0.42em;
    margin-left: -14px;
  }
  .cover-photo {
    position: absolute; left: 262px; top: 112px; width: 670px; height: 560px;
    background:
      radial-gradient(ellipse 38% 30% at 28% 78%, rgba(214,160,110,0.55), transparent 70%),
      radial-gradient(ellipse 34% 26% at 70% 24%, rgba(120,190,230,0.45), transparent 70%),
      radial-gradient(ellipse 30% 24% at 45% 40%, rgba(235,90,70,0.35), transparent 70%),
      radial-gradient(ellipse 34% 22% at 75% 50%, rgba(150,200,80,0.40), transparent 70%),
      radial-gradient(ellipse 30% 22% at 25% 30%, rgba(240,220,80,0.40), transparent 70%),
      radial-gradient(ellipse 50% 45% at 50% 50%, rgba(170,130,160,0.18), transparent 75%);
  }
  .title {
    position: absolute; top: 648px; left: 0; width: 100%;
    font-size: 100px; font-weight: 200; line-height: 104px;
    color: var(--title-grey); letter-spacing: 0.01em; margin-left: -14px;
  }
  .subtitle {
    position: absolute; top: 872px; left: 0; width: 100%;
    font-size: 29px; font-weight: 300; line-height: 40px;
    color: var(--subtitle-ink); margin-left: -14px;
  }
</style>
</head>
<body>
  <main class="book-cover">
    <aside class="spine">
      <div class="spine-title">THE PAPER HERONS</div>
      <div class="spine-author">GORDON WHITLOW</div>
    </aside>
    <section class="front">
      <p class="author">GORDON WHITLOW</p>
      <div class="cover-photo" role="img" aria-label="Photograph of scattered coloured pencils with a sharpener and curled pencil shavings on white"></div>
      <h1 class="title">THE PAPER<br>HERONS</h1>
      <p class="subtitle">CREATIVE PHENOMS WHO<br>RAISE DESIGN TO HIGH ART FORM</p>
    </section>
  </main>
</body>
</html>
```